Business Cards Needed for Innovative Healthcare Marketing Company

We are a marketing company focused on healthcare. Our company is all about rebranding yourself renewing your image and generating results. The phoenix stands for "reborn" or "rising" which we provide new brands for our clients we take their old brands and renew it with creativity and innovation. I am looking for a business card with color dimension. I have attached an example of a card I think has the look and feel of what I am trying to accomplish. I like that the card example has black and grey font colors, I like the font placement and the small logo, I really like the use of the colors on the right those are the colors of my logo. My logo is phoenix so maybe incorporating flames similar to that design. I would like the back a solid color maybe red with an opaque version of the logo and website. As a marketing company I am always open to creative liberty!

Target Market(s)

Doctors and business professionals.

Industry/Entity Type

Marketing

Contact Information for Business Card

Valcorne Health Care Marketing
Marla Tenwick- CEO
#(512)638-2974
email-marla@valcorne.com
website- valcorne.com

Font styles to use
Sans Serif

Colors
ec1f27
f37122
ffc214
fbed22
fbf289
f04a50

Requirements
Must have
• The logo and required information
Nice to have
• icons by the information
Should not have
• child like font

```html
<!DOCTYPE html>
<html lang="en">
<head>
<meta charset="utf-8">
<title>Valcorne Health Care Marketing – Business Cards</title>
<link rel="stylesheet" href="https://fonts.googleapis.com/css2?family=Montserrat:wght@300;400;700&display=swap">
<style>
  :root {
    --canvas-bg: #e9e9eb;
    --card-white: #ffffff;
    --brand-orange: #f59a23;
    --brand-red: #b2343f;
    --brand-flame: #f37122;
    --ink: #111111;
    --ink-soft: #2b2b2b;
    --shadow: rgba(0, 0, 0, 0.22);
  }
  * { box-sizing: border-box; margin: 0; padding: 0; }
  html, body {
    width: 1200px; height: 900px; overflow: hidden;
    background: var(--canvas-bg);
    font-family: "Montserrat", Arial, sans-serif;
  }
  .canvas { position: relative; width: 1200px; height: 900px; }

  .card {
    position: absolute;
    width: 700px; height: 400px;
    border-radius: 26px;
    background: var(--card-white);
    overflow: hidden;
    box-shadow: 0 14px 34px var(--shadow);
  }
  .card--back { left: 110px; top: 30px; }
  .card--front { left: 390px; top: 470px; }

  /* Back side */
  .back-mark {
    position: absolute; left: 50%; top: 46%;
    transform: translate(-50%, -50%);
    display: flex; align-items: center; gap: 14px;
  }
  .mark-dot {
    width: 34px; height: 34px; border-radius: 50%;
    background: var(--brand-flame);
  }
  .back-mark .brand-name {
    font-weight: 300; font-size: 30px; letter-spacing: 3px;
    color: var(--brand-red); text-transform: uppercase;
  }
  .back-web {
    position: absolute; right: 34px; bottom: 30px;
    font-size: 17px; color: var(--brand-red); letter-spacing: 0.5px;
  }

  /* Front side */
  .front-band {
    position: absolute; left: 0; right: 0; top: 205px; bottom: 0;
    background: var(--brand-orange);
  }
  .front-logo {
    position: absolute; left: 40px; top: 88px;
    display: flex; align-items: center; gap: 14px;
  }
  .front-logo .mark-dot { width: 48px; height: 48px; }
  .front-logo .brand-name {
    font-weight: 300; color: var(--brand-red);
    text-transform: uppercase; line-height: 1.15;
  }
  .brand-name__main { display: block; font-size: 40px; letter-spacing: 2px; }
  .brand-name__sub {
    display: block; font-size: 13px; letter-spacing: 1.5px;
    border-top: 1px solid var(--brand-red); padding-top: 4px; margin-top: 2px;
  }
  .front-emblem {
    position: absolute; right: 44px; top: 36px;
    width: 130px; height: 130px; border-radius: 50%;
    background: radial-gradient(circle at 50% 40%, #f7a34a, var(--brand-flame) 60%, #c2412b);
  }

  .holder {
    position: absolute; left: 48px; top: 232px; color: var(--ink);
  }
  .holder__name { font-weight: 700; font-size: 25px; letter-spacing: 1px; text-transform: uppercase; }
  .holder__role { font-size: 15px; color: var(--card-white); margin-top: 2px; }

  .contact-list {
    position: absolute; left: 48px; top: 300px; list-style: none;
  }
  .contact-list li {
    display: flex; align-items: center; gap: 12px;
    font-size: 16px; color: var(--ink-soft); line-height: 1.55;
  }
  .contact-list svg { width: 14px; height: 14px; fill: var(--ink-soft); flex: none; }
</style>
</head>
<body>
<main class="canvas">

  <section class="card card--back" aria-label="Card back">
    <div class="back-mark">
      <span class="mark-dot"></span>
      <span class="brand-name">Valcorne</span>
    </div>
    <p class="back-web">www.valcorne.com</p>
  </section>

  <section class="card card--front" aria-label="Card front">
    <div class="front-band"></div>
    <div class="front-emblem" role="img" aria-label="Brand emblem decoration in red and orange flame tones"></div>

    <div class="front-logo">
      <span class="mark-dot"></span>
      <span class="brand-name">
        <span class="brand-name__main">Valcorne</span>
        <span class="brand-name__sub">Health Care Marketing</span>
      </span>
    </div>

    <div class="holder">
      <h1 class="holder__name">Marla Tenwick</h1>
      <p class="holder__role">CEO</p>
    </div>

    <ul class="contact-list">
      <li>
        <svg viewBox="0 0 24 24" aria-hidden="true"><path d="M6.6 10.8a15.1 15.1 0 0 0 6.6 6.6l2.2-2.2c.3-.3.7-.4 1-.2 1.1.4 2.3.6 3.6.6.6 0 1 .4 1 1V20c0 .6-.4 1-1 1A17 17 0 0 1 3 4c0-.6.4-1 1-1h3.5c.6 0 1 .4 1 1 0 1.3.2 2.5.6 3.6.1.3 0 .7-.2 1z"/></svg>
        (512)638-2974
      </li>
      <li>
        <svg viewBox="0 0 24 24" aria-hidden="true"><path d="M3 5h18v14H3zM5 7v.5l7 4.5 7-4.5V7zm0 2.8V17h14V9.8l-7 4.5z"/></svg>
        marla@valcorne.com
      </li>
      <li>
        <svg viewBox="0 0 24 24" aria-hidden="true"><path d="M12 2a10 10 0 1 0 0 20 10 10 0 0 0 0-20zm6.9 9h-3a15 15 0 0 0-1.3-5.6A8 8 0 0 1 18.9 11zM12 4.1c.9 1.3 1.7 3.6 1.9 6.9h-3.8c.2-3.3 1-5.6 1.9-6.9zM9.4 5.4A15 15 0 0 0 8.1 11h-3a8 8 0 0 1 4.3-5.6zM5.1 13h3a15 15 0 0 0 1.3 5.6A8 8 0 0 1 5.1 13zm6.9 6.9c-.9-1.3-1.7-3.6-1.9-6.9h3.8c-.2 3.3-1 5.6-1.9 6.9zm2.6-1.3a15 15 0 0 0 1.3-5.6h3a8 8 0 0 1-4.3 5.6z"/></svg>
        www.valcorne.com
      </li>
    </ul>
  </section>

</main>
</body>
</html>
```